full stationary design for a modern sleek design company

we are a design company that does modern minimalistic interior design works as well as other design services for high end clients.
we need a full stationary design including and not limited to (double sided business card, letter head, envelopes, documents folder...etc) that reflects the modern style design we do.
sleek modern and minimalistic is the requirements.
Updates

please use the latest attached files as there was a slight modification on the logo Added Wednesday, March 1, 2017

minor update on the logo files in JPG and PSD has been updated kindly follow the new attachments. Added Thursday, March 2, 2017

Target Market(s)

modern minimalist clients

Industry/Entity Type

Design Agency

Requirements
Must have
• the logo
Nice to have
• i like the colors in the colored 3D logo attached
Should not have
• too many colors

```html
<!DOCTYPE html>
<html lang="en">
<head>
<meta charset="utf-8">
<title>Linea Atelier – Business Card</title>
<link rel="stylesheet" href="https://fonts.googleapis.com/css2?family=Open+Sans:wght@400;600;700&display=swap">
<style>
  :root {
    --backdrop: #8a5f41;
    --card-light: #ffffff;
    --card-dark: #333637;
    --ink: #3a3b3d;
    --ink-soft: #4a4b4d;
    --accent: #f3921e;
    --rule: #d6d6d6;
    --on-dark: #ffffff;
  }
  * { margin: 0; padding: 0; box-sizing: border-box; }
  html, body {
    width: 1200px;
    height: 987px;
    overflow: hidden;
    background: var(--backdrop);
    font-family: "Open Sans", Arial, sans-serif;
  }
  .stage { position: relative; width: 1200px; height: 987px; }

  .card {
    position: absolute;
    left: 293px;
    width: 615px;
    height: 350px;
    box-shadow: 0 3px 8px rgba(0,0,0,0.35);
  }
  .card--front { top: 131px; background: var(--card-light); }
  .card--back  { top: 506px; background: var(--card-dark); }

  .wordmark {
    position: absolute;
    left: 0; right: 0;
    display: flex;
    align-items: center;
    justify-content: center;
    gap: 16px;
  }
  .card--front .wordmark { top: 86px; color: var(--ink); }
  .card--back  .wordmark { top: 150px; color: var(--on-dark); }
  .wordmark__square {
    width: 50px; height: 50px;
    background: var(--accent);
    flex: none;
  }
  .wordmark__text { display: flex; flex-direction: column; line-height: 1; }
  .wordmark__name {
    font-weight: 600;
    font-size: 36px;
    letter-spacing: 3px;
  }
  .wordmark__tagline {
    font-weight: 600;
    font-size: 16px;
    letter-spacing: 7.5px;
    margin-top: 6px;
  }

  .identity {
    position: absolute;
    right: 330px;
    top: 186px;
    text-align: right;
    color: var(--ink-soft);
    font-size: 15.5px;
    line-height: 23.5px;
  }
  .identity__name {
    color: var(--accent);
    font-weight: 700;
    font-size: 20px;
    line-height: 26px;
  }
  .identity__role { margin-bottom: 2px; }

  .divider {
    position: absolute;
    left: 302px;
    top: 188px;
    width: 1px;
    height: 94px;
    background: var(--rule);
  }

  .contacts {
    position: absolute;
    left: 318px;
    top: 188px;
    list-style: none;
    color: var(--ink-soft);
    font-size: 15.5px;
  }
  .contacts li {
    display: flex;
    align-items: center;
    height: 23.5px;
  }
  .contacts svg {
    width: 15px; height: 15px;
    margin-right: 8px;
    fill: var(--accent);
    flex: none;
  }
</style>
</head>
<body>
<main class="stage">

  <section class="card card--front" aria-label="Business card front">
    <div class="wordmark">
      <span class="wordmark__square" aria-hidden="true"></span>
      <span class="wordmark__text">
        <span class="wordmark__name">LINEA ATELIER</span>
        <span class="wordmark__tagline">BY MARC DELORME</span>
      </span>
    </div>

    <div class="identity">
      <div class="identity__name">ADAM REYES</div>
      <div class="identity__role">CEO&amp;Founder</div>
      <div>1420 Harbor Street</div>
      <div>Fairview, Oregon 97024</div>
    </div>

    <span class="divider" aria-hidden="true"></span>

    <ul class="contacts">
      <li>
        <svg viewBox="0 0 16 16" aria-hidden="true"><path d="M3.5 1.5l2.5 0 1 3.5-1.8 1.3a8 8 0 0 0 4.5 4.5L11 9l3.5 1v2.5c0 1-1 2-2 2A11 11 0 0 1 1.5 3.5c0-1 1-2 2-2z"/></svg>
        (555) 214 7830
      </li>
      <li>
        <svg viewBox="0 0 16 16" aria-hidden="true"><path d="M4.5 0.5h7a1 1 0 0 1 1 1v13a1 1 0 0 1-1 1h-7a1 1 0 0 1-1-1v-13a1 1 0 0 1 1-1zM5 2.5v9.5h6V2.5zM8 12.8a0.9 0.9 0 1 0 0 1.8 0.9 0.9 0 0 0 0-1.8z"/></svg>
        (555) 309 4417
      </li>
      <li>
        <svg viewBox="0 0 16 16" aria-hidden="true"><path d="M1 3.5h14v9H1zM2.2 4.6L8 9l5.8-4.4z" fill-rule="evenodd"/></svg>
        adam@lineaatelier.com
      </li>
      <li>
        <svg viewBox="0 0 16 16" aria-hidden="true"><path d="M8 1a7 7 0 1 0 0 14A7 7 0 0 0 8 1zm-1 2.3c-.6.8-1.7 1.2-2 2.2.5.8 1.8.5 2.2 1.5-.3 1-1.3 1.5-1 2.7.3 1 .8 1.7.6 2.9A5.2 5.2 0 0 1 3.2 5c1-1 2.3-1.7 3.8-1.7zm2.6.3a5.2 5.2 0 0 1 3.5 6.7c-.7-.3-1-1.2-1.8-1.3-.8 0-1 1-1.8.7-.6-.5 0-1.5-.4-2.2-.5-.6-1.5-.2-1.8-1 0-1 1.6-1.3 2-2.2z"/></svg>
        www.lineaatelier.com
      </li>
    </ul>
  </section>

  <section class="card card--back" aria-label="Business card back">
    <div class="wordmark">
      <span class="wordmark__square" aria-hidden="true"></span>
      <span class="wordmark__text">
        <span class="wordmark__name">LINEA ATELIER</span>
        <span class="wordmark__tagline">BY MARC DELORME</span>
      </span>
    </div>
  </section>

</main>
</body>
</html>
```